Psychiatric Office Needs a Website- 1st Time Ever!

Been in practice since 2003 with no website, but finally ready to dive in. We are Maplecrest Behavioral Healthcare, a mental health outpatient practice based in Fayetteville, Georgia that sees diverse individuals and families from childhood to advanced age for a variety of conditions. We've grown by word of mouth and referral but would now like to have a digital footprint. Be the pioneer of our website and we will be sure to share. We would like to see designs that are modern, animated, fairly colorful, easy to read, and caters to all ages. Also, we would like the design to take the whole page (not be centered) and can be viewed well on phone/tablet. Please see our outline for more information. Our motto/slogan is: Maplecrest Behavioral Healthcare- A step forward in your wellness journey, so the design should try to reflect that.
Updates

Project Deadline Extended
Reason: site in progress

Target Market(s)

Children through elderly

Industry/Entity Type

Medical

Logo Text

Stepping forward in your wellness journey

Number of Pages Required

1 page

Colors

Designer to choose colors to be used in the design.

Requirements
Must have
• Animation or moving pictures.
• Color.
• Concise.
• User friendly
• Diversity in the stock photos

```html
<!DOCTYPE html>
<html lang="en">
<head>
<meta charset="utf-8">
<title>Maplecrest Behavioral Healthcare</title>
<link href="https://fonts.googleapis.com/css2?family=Asap:wght@400;500;600&family=Arimo:wght@400;700&display=swap" rel="stylesheet">
<style>
:root{
  --teal:#74c1ae;
  --teal-dark:#5eae9a;
  --teal-light:#e7f4f0;
  --ink:#333;
  --muted:#666;
  --dark:#2c2c2c;
  --darker:#1f2221;
  --white:#fff;
  --line:#d9d9d9;
}
*{box-sizing:border-box;margin:0;padding:0}
html,body{width:1200px;height:3455px;overflow:hidden}
body{position:relative;background:var(--white);font-family:"Arimo",Arial,sans-serif;color:var(--ink)}
.abs{position:absolute}
.head{font-family:"Asap",Arial,sans-serif}
h1,h2,h3{font-weight:400}

/* header */
.topbar{left:470px;top:0;width:730px;height:50px;background:var(--dark);color:#eee;font-size:14px;display:flex;align-items:center;gap:34px;padding-left:30px}
.topbar span{display:flex;align-items:center;gap:8px}
.brand{left:78px;top:10px;width:112px;height:112px;border-radius:50%;background:var(--teal);border:4px solid var(--white);box-shadow:0 0 0 2px var(--teal);display:flex;align-items:center;justify-content:center;text-align:center;color:var(--white);font-family:"Asap",sans-serif;font-size:13px;line-height:1.25;padding:10px;z-index:2}
.nav{left:0;top:50px;width:1200px;height:70px}
.nav a{position:absolute;top:20px;font-family:"Asap",sans-serif;font-size:17px;color:#444;text-decoration:none}
.nav .active{left:357px;top:-14px;width:97px;height:84px;background:var(--teal);color:var(--white);display:flex;align-items:flex-end;justify-content:center;padding-bottom:22px}

/* hero */
.hero{left:0;top:120px;width:1200px;height:570px;background:linear-gradient(160deg,#9db070 0%,#6f8a52 35%,#c8c2a8 60%,#5d7a52 100%)}
.hero-panel{left:210px;top:180px;width:782px;height:160px;background:rgba(60,60,60,.55)}
.hero h1{left:0;top:180px;width:1200px;text-align:center;font-family:"Asap",sans-serif;font-size:50px;color:var(--white)}
.hero .tag{left:0;top:240px;width:1200px;text-align:center;font-family:"Asap",sans-serif;font-style:italic;font-size:22px;color:var(--white)}
.btn{background:var(--teal);color:var(--white);font-family:"Asap",sans-serif;display:flex;align-items:center;justify-content:center;text-transform:uppercase}
.hero .btn{left:506px;top:288px;width:188px;height:52px;font-size:20px}

/* vision / mission */
.vm-left{left:0;top:690px;width:600px;height:370px;background:var(--teal)}
.vm-title{font-family:"Asap",sans-serif;font-size:34px;display:flex;align-items:center;gap:14px}
.vm-text{font-size:15px;line-height:1.55;width:350px}
.vm-seal{left:455px;top:718px;width:290px;height:290px;border-radius:50%;background:var(--teal);border:8px solid var(--white);box-shadow:0 0 0 3px var(--teal);display:flex;align-items:center;justify-content:center;text-align:center;color:var(--white);font-family:"Asap",sans-serif;font-size:24px;line-height:1.3;padding:40px}

/* services */
.services{left:0;top:1060px;width:1200px;height:833px;background:linear-gradient(135deg,#3b3836 0%,#26292a 45%,#3a3937 75%,#2b2b2c 100%)}
.sec-title{font-family:"Asap",sans-serif;font-size:36px;color:var(--white);text-align:center;width:1200px;left:0;text-transform:uppercase}
.svc{width:300px;color:var(--white);font-size:13px;line-height:1.5}
.svc h3{font-family:"Asap",sans-serif;color:var(--teal);font-size:17px;margin-bottom:4px}
.svc b{text-decoration:underline;font-size:12px}

/* conditions */
.conditions{left:0;top:1893px;width:1200px;height:553px;background:var(--teal)}
.card-img{width:250px;height:168px;box-shadow:5px 5px 8px rgba(0,0,0,.3)}
.card-label{width:250px;text-align:center;font-family:"Asap",sans-serif;font-size:21px;color:var(--white);line-height:1.1}
.card-text{width:250px;text-align:center;font-size:13px;line-height:1.45;color:var(--white)}
.arrow{width:30px;height:34px;background:var(--white);border:1px solid #ccc;display:flex;align-items:center;justify-content:center}

/* faq & news */
.h2{font-family:"Asap",sans-serif;font-size:37px;color:var(--teal)}
.faq-item{left:78px;width:520px;border:1px solid var(--line);font-family:"Asap",sans-serif;font-size:20px;color:var(--teal);display:flex;align-items:center;gap:12px;padding-left:14px}
.news-title{font-family:"Asap",sans-serif;font-size:19px;color:var(--teal)}
.news-meta{font-size:12px;color:#888}
.news-text{font-size:14px;color:#555;line-height:1.45;width:330px}
.more{font-size:13px;color:var(--teal);letter-spacing:.5px}

/* cta */
.cta{left:0;top:2874px;width:1200px;height:104px;background:var(--teal)}

/* footer */
.footer{left:0;top:2978px;width:1200px;height:407px;background:linear-gradient(120deg,#4a2b22 0%,#2d2523 40%,#5a3a2a 70%,#2a2421 100%)}
.footer-shade{left:0;top:2978px;width:1200px;height:407px;background:rgba(20,20,20,.55)}
.f-head{font-family:"Asap",sans-serif;font-size:21px;color:var(--white);text-transform:uppercase;letter-spacing:.5px}
.field{left:78px;width:449px;height:42px;background:var(--white);font-size:14px;color:#555;padding:10px 12px}
.f-list li{list-style:none;color:var(--white);font-size:15px;margin-bottom:11px;display:flex;align-items:center;gap:10px}
.f-list li::before{content:"";width:7px;height:7px;border-radius:50%;background:var(--teal)}
.find{color:var(--white);font-size:15px;line-height:1.5;display:flex;gap:14px;align-items:flex-start}
.social{width:52px;height:52px;border-radius:50%;background:var(--teal)}
.bottombar{left:0;top:3385px;width:1200px;height:70px;background:var(--darker);border-top:1px solid #555;color:var(--white);font-family:"Asap",sans-serif;font-size:15px;display:flex;align-items:center;justify-content:center}
</style>
</head>
<body>

<!-- header -->
<div class="abs topbar">
  <span><svg width="18" height="18" viewBox="0 0 18 18"><circle cx="9" cy="9" r="7.5" fill="none" stroke="#eee" stroke-width="1.6"/><path d="M9 4.5V9l3 2" stroke="#eee" stroke-width="1.6" fill="none"/></svg>Monday - Friday : 10.00 A.M to 8.00 P.M</span>
  <span><svg width="18" height="18" viewBox="0 0 18 18"><path d="M4 2l3 3-2 2c1 2 3 4 5 5l2-2 3 3-2 3C7 15 3 11 1 5z" fill="#eee"/></svg>+1-555-014-2260</span>
  <span>LOGIN <svg width="16" height="18" viewBox="0 0 16 18"><circle cx="8" cy="5" r="4" fill="#74c1ae"/><path d="M0 18c0-5 4-7 8-7s8 2 8 7z" fill="#74c1ae"/></svg> Patient</span>
</div>
<div class="abs brand">Maplecrest Behavioral Healthcare</div>
<nav class="abs nav">
  <a class="active" href="#">Home</a>
  <a href="#" style="left:505px">About Us</a>
  <a href="#" style="left:607px">Services</a>
  <a href="#" style="left:700px">Conditions We Treat</a>
  <a href="#" style="left:888px">New Patients</a>
  <a href="#" style="left:1022px">Contact Us</a>
</nav>

<!-- hero -->
<section class="abs hero" role="img" aria-label="Photo of four smiling young volunteers holding a globe together">
  <div class="abs hero-panel"></div>
  <h1 class="abs">Maplecrest Behavioral Healthcare</h1>
  <p class="abs tag">A step forward in your wellness journey</p>
  <a class="abs btn">Contact Us</a>
</section>

<!-- vision & mission -->
<section>
  <div class="abs vm-left"></div>
  <div class="abs" style="left:78px;top:735px;color:var(--white)">
    <h2 class="vm-title"><svg width="30" height="34" viewBox="0 0 30 34"><path d="M6 16l16-10 3 5-16 10z" fill="#fff"/><path d="M12 20l-6 13M14 20l5 13" stroke="#fff" stroke-width="2.5"/></svg>VISION</h2>
    <div style="width:160px;height:2px;background:#fff;margin:8px 0 24px"></div>
    <p class="vm-text">Lorem Ipsum is simply dummy text of the printing and typesetting industry. Lorem Ipsum has been the industry's standard dummy text ever since the 1500s, when an unknown printer took a galley of type and scrambled it to make a type specimen book. It has survived not only five centuries, but also the leap into electronic typesetting, remaining essentially unchanged.</p>
  </div>
  <div class="abs vm-seal">Maplecrest Behavioral Healthcare</div>
  <div class="abs" style="left:768px;top:735px">
    <h2 class="vm-title" style="color:var(--teal)"><svg width="34" height="34" viewBox="0 0 34 34"><circle cx="16" cy="18" r="13" fill="none" stroke="#74c1ae" stroke-width="3"/><circle cx="16" cy="18" r="6" fill="none" stroke="#74c1ae" stroke-width="3"/><path d="M16 18L31 3" stroke="#74c1ae" stroke-width="3"/></svg>MISSION</h2>
    <div style="width:0;height:2px;margin:8px 0 24px"></div>
    <p class="vm-text" style="color:#555">Lorem Ipsum is simply dummy text of the printing and typesetting industry. Lorem Ipsum has been the industry's standard dummy text ever since the 1500s, when an unknown printer took a galley of type and scrambled it to make a type specimen book. It has survived not only five centuries, but also the leap into electronic typesetting, remaining essentially unchanged.</p>
  </div>
</section>

<!-- services -->
<section class="abs services" role="img" aria-label="Blurred photo of a counsellor meeting a client, darkened as background">
  <h2 class="abs sec-title" style="top:46px">Services</h2>
  <div class="abs" style="left:520px;top:102px;width:160px;height:2px;background:#fff"></div>
  <svg class="abs" style="left:0;top:0" width="1200" height="833" viewBox="0 0 1200 833">
    <g stroke="#74c1ae" stroke-width="2" fill="#74c1ae">
      <line x1="598" y1="386" x2="497" y2="205"/><line x1="598" y1="386" x2="690" y2="193"/>
      <line x1="598" y1="386" x2="396" y2="357"/><line x1="598" y1="386" x2="798" y2="336"/>
      <line x1="598" y1="386" x2="444" y2="529"/><line x1="598" y1="386" x2="798" y2="517"/>
      <line x1="598" y1="386" x2="607" y2="602"/>
      <circle cx="548" cy="296" r="5"/><circle cx="642" cy="293" r="5"/><circle cx="496" cy="372" r="5"/>
      <circle cx="698" cy="361" r="5"/><circle cx="523" cy="456" r="5"/><circle cx="685" cy="443" r="5"/><circle cx="602" cy="489" r="5"/>
    </g>
    <circle cx="598" cy="386" r="103" fill="#e9e9e9" stroke="#74c1ae" stroke-width="4"/>
    <g fill="#74c1ae" stroke="#fff" stroke-width="5">
      <circle cx="497" cy="205" r="62"/><circle cx="690" cy="193" r="62"/><circle cx="396" cy="357" r="62"/>
      <circle cx="798" cy="336" r="62"/><circle cx="444" cy="529" r="62"/><circle cx="798" cy="517" r="62"/><circle cx="607" cy="602" r="62"/>
    </g>
    <g fill="#c9b7a8">
      <circle cx="497" cy="205" r="53"/><circle cx="690" cy="193" r="53"/><circle cx="396" cy="357" r="53"/>
      <circle cx="798" cy="336" r="53"/><circle cx="444" cy="529" r="53"/><circle cx="798" cy="517" r="53"/><circle cx="607" cy="602" r="53"/>
    </g>
  </svg>
  <div class="abs svc" style="left:138px;top:158px"><h3>Diagnostic evaluation and treatment</h3>Lorem Ipsum is simply dummy text<br>of the printing and text typesetting<br>industry.<b>READ MORE</b></div>
  <div class="abs svc" style="left:78px;top:327px"><h3>Psychopharmacology</h3>Lorem Ipsum is simply dummy text<br>of the printing and text typesetting<br>industry.<b>READ MORE</b></div>
  <div class="abs svc" style="left:101px;top:514px"><h3>Bariatric pre-surgical consultation</h3>Lorem Ipsum is simply dummy text<br>of the printing and text typesetting<br>industry.<b>READ MORE</b></div>
  <div class="abs svc" style="left:500px;top:692px"><h3>Developmental disabilities</h3>Lorem Ipsum is simply dummy<br>text of the printing and text<br>typesetting industry.<b>READ MORE</b></div>
  <div class="abs svc" style="left:771px;top:140px"><h3>Disability and work-related reports</h3>Lorem Ipsum is simply dummy text<br>of the printing and text typesetting<br>industry.<b>READ MORE</b></div>
  <div class="abs svc" style="left:888px;top:296px"><h3>Early childhood Assessments</h3>Lorem Ipsum is simply dummy text of<br>the printing and text typesetting<br>industry.<b>READ MORE</b></div>
  <div class="abs svc" style="left:866px;top:484px"><h3>Substance abuse assessments</h3>Lorem Ipsum is simply dummy text of<br>the printing and text typesetting<br>industry.<b>READ MORE</b></div>
</section>

<!-- conditions -->
<section class="abs conditions">
  <h2 class="abs sec-title" style="top:58px">Conditiond We Treat</h2>
  <div class="abs" style="left:480px;top:110px;width:240px;height:2px;background:#fff"></div>
  <div class="abs card-img" style="left:78px;top:150px;background:linear-gradient(135deg,#222,#6b5a52)" role="img" aria-label="Photo of a distressed woman holding her head"></div>
  <div class="abs card-img" style="left:343px;top:150px;background:linear-gradient(135deg,#c9b49d,#4a7aa8)" role="img" aria-label="Photo of a nurse comforting a patient"></div>
  <div class="abs card-img" style="left:608px;top:150px;background:linear-gradient(135deg,#b5aaa0,#6d6460)" role="img" aria-label="Photo of a worried elderly man with a caregiver"></div>
  <div class="abs card-img" style="left:873px;top:150px;background:linear-gradient(135deg,#8a5a3e,#d9b79a)" role="img" aria-label="Photo of a mother hugging her child"></div>
  <div class="abs card-label" style="left:78px;top:338px">Mood Disorders</div>
  <div class="abs card-label" style="left:343px;top:338px">Anxiety Disorders</div>
  <div class="abs card-label" style="left:608px;top:338px">Psychotic Disorders</div>
  <div class="abs card-label" style="left:873px;top:326px">Common Disorders<br>of Childhood</div>
  <p class="abs card-text" style="left:78px;top:385px">Lorem Ipsum is simply dummy text of the printing and typesetting industry. Lorem Ipsum has been the industry's standard dummy text ever since.</p>
  <p class="abs card-text" style="left:343px;top:385px">Lorem Ipsum is simply dummy text of the printing and typesetting industry. Lorem Ipsum has been the industry's standard dummy text ever since.</p>
  <p class="abs card-text" style="left:608px;top:385px">Lorem Ipsum is simply dummy text of the printing and typesetting industry. Lorem Ipsum has been the industry's standard dummy text ever since.</p>
  <p class="abs card-text" style="left:873px;top:385px">Lorem Ipsum is simply dummy text of the printing and typesetting industry. Lorem Ipsum has been the industry's standard dummy text ever since.</p>
  <div class="abs arrow" style="left:31px;top:211px"><svg width="10" height="14"><path d="M8 1L2 7l6 6" stroke="#666" stroke-width="2" fill="none"/></svg></div>
  <div class="abs arrow" style="left:1139px;top:211px"><svg width="10" height="14"><path d="M2 1l6 6-6 6" stroke="#666" stroke-width="2" fill="none"/></svg></div>
  <div class="abs" style="left:572px;top:516px;display:flex;gap:4px">
    <span style="width:14px;height:14px;border:2px solid #fff"></span><span style="width:14px;height:14px;background:#fff"></span><span style="width:14px;height:14px;border:2px solid #fff"></span>
  </div>
</section>

<!-- FAQ -->
<h2 class="abs h2" style="left:78px;top:2490px">FAQ</h2>
<div class="abs" style="left:78px;top:2556px;width:520px;height:127px;border:1px solid var(--line)"></div>
<div class="abs faq-item" style="top:2556px;height:44px;border:none;border-bottom:1px solid var(--line)"><svg width="18" height="18"><rect y="7" width="18" height="4" fill="#74c1ae"/></svg>What do I need to bring with me to my first visit?</div>
<p class="abs" style="left:94px;top:2608px;width:490px;font-size:12px;line-height:1.5;color:#555">Lorem Ipsum is simply dummy text of the printing and typesetting industry. Lorem Ipsum has been the industry's standard dummy text ever since the 1500s,It has survived not only five centuries, but also the leap into electronic typesetting, remaining essentially unchanged.</p>
<div class="abs faq-item" style="top:2685px;height:42px"><svg width="18" height="18"><path d="M7 0h4v18H7zM0 7h18v4H0z" fill="#74c1ae"/></svg>How long do I have to wait to be seen?</div>
<div class="abs faq-item" style="top:2727px;height:42px;border-top:none"><svg width="18" height="18"><path d="M7 0h4v18H7zM0 7h18v4H0z" fill="#74c1ae"/></svg>Why is my child not doing well in school?</div>
<div class="abs faq-item" style="top:2769px;height:42px;border-top:none"><svg width="18" height="18"><path d="M7 0h4v18H7zM0 7h18v4H0z" fill="#74c1ae"/></svg>What typs of insurance do you accept?</div>
<div class="abs" style="left:608px;top:2446px;width:10px;height:428px;background:#eee"></div>

<!-- news -->
<h2 class="abs h2" style="left:668px;top:2490px">LATEST NEWS</h2>
<div class="abs" style="left:668px;top:2552px;width:115px;height:110px;background:linear-gradient(135deg,#c7b59d,#3e5f8a)" role="img" aria-label="Photo of a stressed young woman"></div>
<div class="abs" style="left:799px;top:2552px">
  <div class="news-title">Lorem Ipsum is simply dummy text</div>
  <div class="news-meta" style="margin:6px 0">&#9635; 10 JULY 2016</div>
  <p class="news-text">Lorem Ipsum is simply dummy text of the printing and typesetting industry......</p>
  <div class="more" style="margin-top:10px">READ MORE &nbsp; &#187;</div>
</div>
<div class="abs" style="left:668px;top:2692px;width:470px;height:1px;background:var(--line)"></div>
<div class="abs" style="left:668px;top:2713px;width:115px;height:110px;background:linear-gradient(135deg,#d8c8a8,#5b4a3a)" role="img" aria-label="Photo of a child reading with a parent"></div>
<div class="abs" style="left:799px;top:2713px">
  <div class="news-title">Lorem Ipsum is simply dummy text</div>
  <div class="news-meta" style="margin:6px 0">&#9635; 10 JULY 2016</div>
  <p class="news-text">Lorem Ipsum is simply dummy text of the printing and typesetting industry......</p>
  <div class="more" style="margin-top:10px">READ MORE &nbsp; &#187;</div>
</div>

<!-- call to action -->
<section class="abs cta">
  <p class="abs" style="left:78px;top:30px;width:780px;color:#fff;font-size:15px;line-height:1.6">Lorem Ipsum is simply dummy text of the printing and typesetting industry. Lorem Ipsum has been the industry's standard dummy text ever since the 1500s, when an unknown printer took a galley of type and scrambled.</p>
  <div class="abs head" style="left:894px;top:28px;width:228px;height:53px;background:#fff;color:#333;font-size:19px;display:flex;align-items:center;justify-content:center">NEW PATIENT FORM</div>
</section>

<!-- footer -->
<div class="abs footer" role="img" aria-label="Warm blurred photo of autumn leaves, darkened as background"></div>
<div class="abs footer-shade"></div>
<h3 class="abs f-head" style="left:78px;top:3036px">Quick Inquiry</h3>
<div class="abs field" style="top:3084px">Name*</div>
<div class="abs field" style="top:3130px">Email*</div>
<div class="abs field" style="top:3176px">Services*</div>
<div class="abs field" style="top:3222px;height:95px">Message*</div>
<div class="abs btn" style="left:78px;top:3326px;width:184px;height:50px;font-size:19px">Submit</div>

<h3 class="abs f-head" style="left:569px;top:3036px">Our Services</h3>
<ul class="abs f-list" style="left:569px;top:3080px">
  <li>Home</li><li>About Us</li><li>Services</li><li>Conditions We Treat</li><li>New Patients</li><li>Contact Us</li>
</ul>

<h3 class="abs f-head" style="left:873px;top:3036px">Find Us</h3>
<div class="abs find" style="left:873px;top:3080px"><svg width="18" height="24" viewBox="0 0 18 24"><path d="M9 0a9 9 0 019 9c0 6-9 15-9 15S0 15 0 9a9 9 0 019-9z" fill="#74c1ae"/><circle cx="9" cy="9" r="3.5" fill="#2d2523"/></svg><span>Maplecrest Behavioral Healthcare<br>Lorem Ipsum is simply dummy<br>text printing and typesetting</span></div>
<div class="abs find" style="left:873px;top:3172px"><svg width="22" height="22" viewBox="0 0 18 18"><path d="M4 2l3 3-2 2c1 2 3 4 5 5l2-2 3 3-2 3C7 15 3 11 1 5z" fill="#74c1ae"/></svg><span>+1-555-014-2260</span></div>
<div class="abs find" style="left:873px;top:3215px"><svg width="22" height="22" viewBox="0 0 22 22"><rect x="3" y="1" width="16" height="9" fill="#74c1ae"/><rect x="1" y="10" width="20" height="11" rx="2" fill="#74c1ae"/></svg><span>+1-555-014-2260</span></div>
<div class="abs find" style="left:873px;top:3258px"><svg width="22" height="18" viewBox="0 0 22 18"><rect width="22" height="18" rx="2" fill="#74c1ae"/><path d="M1 2l10 8 10-8" stroke="#2d2523" stroke-width="2" fill="none"/></svg><span>info@maplecresthealth.com</span></div>
<div class="abs social" style="left:873px;top:3306px"></div>
<div class="abs social" style="left:935px;top:3306px"></div>
<div class="abs social" style="left:997px;top:3306px"></div>

<footer class="abs bottombar">&#169; MAPLECREST BEHAVIORAL HEALTHCARE- 2017. All Rights Reserved</footer>

</body>
</html>
```